School Hallway Magnetic Display Design for school values

I am looking for a someone to help me design a magnetic hallway display that will hang in the hallway of our small school. There are several elements, including 1. 6ft by 4ft designed magnetic bulletin board, 2. Magnets that will stick to the board. See attachment for which elements belong where. The display will be for our MOBLAT program, which rewards students for demonstrating our school values. We want the display to be beautiful and interactive. We are also rebranding, so we want the design to align with our new fonts and colors. In the attached PDF is an outline of our new brand guidelines. Unfortunately, we don't have the color codes, but I'm hoping that you can match the colors listed. Attached are elements to be used on the board, but please use your creativity to make it more dynamic and visually appealing. For example, the star magnets could be another shape. The MOBLAT magnets must remain the same. I've included two photos of boards at other schools that inspired this project.

Target Market(s)

School Community

Industry/Entity Type

Education

Requirements
Should not have
• School Logo

```html
<!DOCTYPE html>
<html lang="en">
<head>
<meta charset="utf-8">
<title>MOBLAT of the Month – Hallway Magnetic Display</title>
<link rel="stylesheet" href="https://fonts.googleapis.com/css2?family=Lora:wght@600&family=Arimo:wght@700&family=Montserrat:wght@700;800&display=swap">
<style>
  :root {
    --page-bg: #efe9dc;
    --green-deep: #24502a;
    --green-mid: #5f8f2a;
    --green-lime: #a7bd34;
    --cream: #e6dca3;
    --slate: #8fa3b8;
    --board-white: #f4f4f2;
    --title-pill: #eeeeec;
    --ink: #1d3527;
    --ink-dark: #1b1b1b;
    --magnet-face: #f3f3f1;
    --star-gold: #f6c21c;
    --note-green: #33d12e;
  }
  * { box-sizing: border-box; margin: 0; padding: 0; }
  html, body { width: 1200px; height: 950px; overflow: hidden; }
  body { background: var(--page-bg); position: relative; font-family: "Arimo", Arial, sans-serif; }

  .board {
    position: absolute; left: 122px; top: 155px; width: 1038px; height: 652px;
    background: linear-gradient(135deg, var(--green-mid) 0%, var(--green-lime) 30%, var(--green-deep) 55%, var(--cream) 75%, var(--green-mid) 100%);
  }
  .board-pattern { position: absolute; inset: 0; }
  .title-pill {
    position: absolute; left: 23px; top: 24px; width: 640px; height: 98px;
    background: var(--title-pill); border-radius: 0 22px 22px 0;
    display: flex; align-items: center; padding-left: 24px;
    font-family: "Lora", Georgia, serif; font-weight: 600; font-size: 54px; color: var(--ink);
    letter-spacing: -0.5px; white-space: nowrap; overflow: hidden;
  }
  .whiteboard {
    position: absolute; left: 23px; top: 160px; width: 774px; height: 379px;
    background: var(--board-white);
  }
  .thermometer { position: absolute; left: 655px; top: 50px; width: 125px; height: 460px; }

  .word-magnet {
    position: absolute; height: 64px; background: var(--magnet-face);
    border: 3px solid var(--ink-dark); border-radius: 5px;
    box-shadow: 2px 3px 4px rgba(0,0,0,0.25);
    display: flex; align-items: center; justify-content: center;
    font-weight: 700; font-size: 31px; color: var(--ink-dark); white-space: nowrap;
  }

  .star { position: absolute; width: 66px; height: 64px; }

  .note {
    position: absolute; font-family: "Montserrat", Arial, sans-serif; font-weight: 800;
    color: var(--note-green); text-shadow: 0 0 6px #fff, 0 0 10px #fff; line-height: 1.15;
    white-space: nowrap;
  }
  .note-center { text-align: center; }
  .dimension { position: absolute; }
</style>
</head>
<body>

  <section class="board" aria-label="MOBLAT of the Month magnetic board">
    <div class="board-pattern" role="img" aria-label="Geometric green, lime and cream block pattern border"></div>
    <div class="whiteboard"></div>
    <h1 class="title-pill">MOBLAT of the Month</h1>
    <svg class="thermometer" viewBox="0 0 125 460" aria-label="Thermometer graphic">
      <path d="M42 24 a20 20 0 0 1 40 0 V340 a54 54 0 1 1 -40 0 Z" fill="var(--board-white)" stroke="var(--ink-dark)" stroke-width="8"/>
      <path d="M78 370 a32 32 0 0 1 -8 56" fill="none" stroke="var(--ink-dark)" stroke-width="7" stroke-linecap="round"/>
      <g stroke="var(--ink-dark)" stroke-width="6" stroke-linecap="round">
        <line x1="42" y1="48" x2="62" y2="48"/>
        <line x1="42" y1="84" x2="62" y2="84"/>
        <line x1="42" y1="120" x2="62" y2="120"/>
        <line x1="42" y1="156" x2="62" y2="156"/>
        <line x1="42" y1="192" x2="62" y2="192"/>
        <line x1="42" y1="228" x2="62" y2="228"/>
        <line x1="42" y1="264" x2="62" y2="264"/>
        <line x1="42" y1="300" x2="62" y2="300"/>
      </g>
    </svg>
  </section>

  <div class="word-magnet" style="left:980px; top:226px; width:192px;">Simplicity</div>
  <div class="word-magnet" style="left:980px; top:306px; width:192px;">Peace</div>
  <div class="word-magnet" style="left:980px; top:384px; width:192px;">Integrity</div>
  <div class="word-magnet" style="left:967px; top:464px; width:215px;">Community</div>
  <div class="word-magnet" style="left:980px; top:544px; width:192px;">Equality</div>
  <div class="word-magnet" style="left:962px; top:622px; width:228px;">Stewardship</div>

  <svg width="0" height="0" style="position:absolute">
    <defs>
      <symbol id="star-shape" viewBox="0 0 100 96">
        <polygon points="50,2 62,36 98,37 69,58 80,93 50,72 20,93 31,58 2,37 38,36" fill="var(--star-gold)"/>
      </symbol>
    </defs>
  </svg>

  <svg class="star" style="left:497px; top:715px;"><use href="#star-shape"/></svg>
  <svg class="star" style="left:577px; top:715px;"><use href="#star-shape"/></svg>
  <svg class="star" style="left:657px; top:715px;"><use href="#star-shape"/></svg>
  <svg class="star" style="left:738px; top:715px;"><use href="#star-shape"/></svg>
  <svg class="star" style="left:842px; top:715px;"><use href="#star-shape"/></svg>
  <svg class="star" style="left:925px; top:715px;"><use href="#star-shape"/></svg>

  <svg class="star" style="left:497px; top:815px;"><use href="#star-shape"/></svg>
  <svg class="star" style="left:577px; top:815px;"><use href="#star-shape"/></svg>
  <svg class="star" style="left:657px; top:815px;"><use href="#star-shape"/></svg>
  <svg class="star" style="left:738px; top:815px;"><use href="#star-shape"/></svg>

  <svg class="star" style="left:497px; top:893px;"><use href="#star-shape"/></svg>
  <svg class="star" style="left:577px; top:893px;"><use href="#star-shape"/></svg>
  <svg class="star" style="left:657px; top:893px;"><use href="#star-shape"/></svg>
  <svg class="star" style="left:738px; top:893px;"><use href="#star-shape"/></svg>

  <svg class="dimension" style="left:0; top:0;" width="1200" height="950" aria-hidden="true">
    <g stroke="var(--note-green)" stroke-width="2">
      <line x1="122" y1="166" x2="930" y2="166"/>
      <line x1="136" y1="172" x2="136" y2="690"/>
      <line x1="220" y1="112" x2="282" y2="205"/>
    </g>
  </svg>

  <div class="note" style="left:65px; top:80px; font-size:28px;">PRINTED TITLE</div>
  <div class="note" style="left:514px; top:120px; font-size:34px;">72 in</div>
  <div class="note" style="left:80px; top:420px; font-size:34px; transform:rotate(-90deg); transform-origin:left top;">48 in</div>
  <div class="note" style="left:958px; top:130px; font-size:30px;">6”x21” Word<br>Magnets</div>
  <div class="note note-center" style="left:240px; top:445px; width:330px; font-size:30px;">Open Whiteboard<br>for Magnets</div>
  <div class="note note-center" style="left:570px; top:410px; width:250px; font-size:28px;">Thermometer<br>Graphic<br>(Printed)</div>
  <div class="note note-center" style="left:320px; top:732px; width:170px; font-size:28px;">6” Star<br>Magnets</div>

</body>
</html>
```